Motor Oil Lubricant Package Labels

We are looking for a logo and label that we can put on our motor oil bottle 1 liter and 5 liter. The name of our motor oil is Corvana. We want to design our flagship logo for CORVANA MOTOR OILS and as well as the label that will go on the bottle. We have some drafts that we have come up with attached and would like to see more options. The concept of a timeless motor oil and the endless loop of lubricating oils incorporated in the design. We will have full synthetic motor oil, a synthetic blend motor, ATF III transmission fluid, KRL-VI transmission fluid. hydraulic oils etc. Examples will be attached
Target Market(s)
Automotive Lubricants and Chemicals
Industry/Entity Type
Automotive
Logo Text
Corvana Lubricants
Font styles to use
Other font styles liked:
- Let designer choose
Requirements
Must have
- The Corvana sign incorporated in a very cool way to our name. Our brand needs to stick out
Nice to have
- Automotive lubricant related and colors red, white, and blue incorporated in the design
Should not have
- Images of individuals and or topics not related to automotive lubricants.

```html
<!DOCTYPE html>
<html lang="en">
<head>
<meta charset="utf-8">
<title>Corvana Motor Oil – Bottle Labels</title>
<link rel="stylesheet" href="https://fonts.googleapis.com/css2?family=Anton&family=Archivo+Black&family=Roboto+Condensed:wght@300;400;700&family=Russo+One&display=swap">
<style>
  :root{
    --red:#e41e26;
    --blue:#2753a8;
    --ink:#231f20;
    --white:#ffffff;
    --silver-1:#f4f4f4;
    --silver-2:#c9c9c9;
    --silver-3:#e6e6e6;
    --gold-1:#f7d46a;
    --gold-2:#b8860b;
  }
  *{margin:0;padding:0;box-sizing:border-box}
  html,body{width:1200px;height:852px;overflow:hidden;background:var(--white)}
  .canvas{position:relative;width:1200px;height:852px;background:var(--white)}
  .label{position:absolute;top:47px;width:467px;height:760px;border-radius:34px;overflow:hidden;
    background:linear-gradient(100deg,var(--silver-2) 0%,var(--silver-1) 35%,var(--silver-3) 60%,var(--silver-2) 100%)}
  .label--front{left:105px}
  .label--back{left:628px}
  .label__art{position:absolute;inset:0;width:467px;height:760px}
  .abs{position:absolute}
  .brand-name{font-family:"Russo One",sans-serif;color:var(--blue);letter-spacing:1px;line-height:1}
  .brand-dot{position:absolute;border-radius:50%;background:var(--red)}
  .brand-sub{font-family:"Russo One",sans-serif;color:var(--blue);line-height:1}
  .synthetic{font-family:"Russo One",sans-serif;color:var(--white);-webkit-text-stroke:1.2px var(--ink);letter-spacing:1px;line-height:1;white-space:nowrap}
  .advanced{font-family:"Russo One",sans-serif;color:var(--blue);line-height:1;white-space:nowrap;text-shadow:0 0 2px var(--white),0 0 2px var(--white)}
  .performance{font-family:"Russo One",sans-serif;color:var(--white);background:var(--red);line-height:1;white-space:nowrap;text-align:center}
  .tagline{font-family:"Russo One",sans-serif;color:var(--ink);font-size:11.5px;line-height:15px;text-align:center;letter-spacing:.5px}
  .seal{position:absolute;border-radius:50%;
    background:radial-gradient(circle at 40% 35%,var(--gold-1) 0%,#e0ac33 55%,var(--gold-2) 100%);
    box-shadow:0 2px 5px rgba(0,0,0,.35)}
  .seal::after{content:"";position:absolute;inset:18%;border-radius:50%;background:var(--white);box-shadow:inset 0 0 3px rgba(0,0,0,.3)}
  .volume{font-family:"Roboto Condensed",sans-serif;font-weight:700;font-size:26px;color:var(--ink);line-height:1}
  .made-usa{font-family:"Roboto Condensed",sans-serif;font-weight:700;font-size:22px;color:var(--white);line-height:1;text-align:center}
  .made-usa small{display:block;font-size:11px;letter-spacing:3px}
  .grade-sae{font-family:"Archivo Black",sans-serif;color:var(--white);font-size:35px;line-height:1}
  .grade-big{font-family:"Anton",sans-serif;color:var(--white);font-size:118px;line-height:.8;white-space:nowrap;transform-origin:0 0;transform:rotate(90deg)}
  .grade-spec{font-family:"Archivo Black",sans-serif;color:var(--white);font-size:26px;line-height:1;white-space:nowrap;transform-origin:0 0;transform:rotate(90deg)}
  .mini-grade{font-family:"Anton",sans-serif;color:var(--blue);font-size:40px;line-height:1;-webkit-text-stroke:1px var(--white)}
  .mini-sae{font-family:"Archivo Black",sans-serif;color:var(--blue);font-size:10px;transform-origin:0 0;transform:rotate(-90deg)}
  .mini-spec{font-family:"Archivo Black",sans-serif;color:var(--blue);font-size:8px}
  .copy{font-family:"Roboto Condensed",sans-serif;font-weight:300;color:var(--ink)}
  .copy--main{left:16px;top:162px;width:436px;font-size:16.4px;line-height:20.4px;text-align:justify}
  .copy--main p{margin:0}
  .copy .hl-red{color:var(--red);font-weight:700}
  .copy .hl-blue{color:var(--blue);font-weight:700}
  .copy b{font-weight:700}
  .benefits{list-style:none;margin:0}
  .benefits li{color:var(--blue);font-weight:700;position:relative;padding-left:42px}
  .benefits li::before{content:"•";position:absolute;left:0;color:var(--blue)}
  .copy--small{left:16px;width:324px;font-size:12.6px;line-height:16.3px;font-weight:400;text-align:justify}
  .copy--small .title{font-weight:700;text-transform:uppercase}
  .sus{font-family:"Anton",sans-serif;color:var(--white);font-size:22px;line-height:1;letter-spacing:.5px}
  .spec-box{background:var(--white)}
  .flag{position:absolute;width:100px;height:52px;
    background:repeating-linear-gradient(180deg,var(--red) 0 4px,var(--white) 4px 8px)}
  .flag::before{content:"";position:absolute;left:0;top:0;width:44px;height:28px;background:var(--blue)}
  .flag-caption{font-family:"Roboto Condensed",sans-serif;font-weight:400;font-size:13px;color:var(--ink);background:var(--white);text-align:center;line-height:16px;letter-spacing:1px}
</style>
</head>
<body>
<main class="canvas">

  <!-- FRONT LABEL -->
  <section class="label label--front" aria-label="Front label">
    <svg class="label__art" viewBox="0 0 467 760" aria-hidden="true">
      <path d="M240 0H467V92C420 50 340 14 240 0Z" fill="var(--blue)"/>
      <path d="M95 0H240C340 14 420 50 467 92V150C405 75 270 20 95 0Z" fill="var(--red)"/>
      <path d="M150 760C165 585 250 420 405 318C335 420 300 565 345 760Z" fill="var(--red)"/>
      <path d="M467 128C390 180 332 282 304 400C282 505 292 640 345 760H400C430 742 455 722 467 700Z" fill="var(--blue)"/>
      <path d="M400 760C430 742 455 722 467 700V760Z" fill="var(--red)"/>
    </svg>

    <div class="brand-dot" style="left:56px;top:166px;width:20px;height:20px"></div>
    <div class="abs brand-name" style="left:84px;top:158px;font-size:44px">CORVANA</div>
    <div class="abs brand-sub" style="left:200px;top:229px;font-size:17px">MOTOR OIL</div>

    <div class="abs synthetic" style="left:0;width:352px;text-align:center;top:267px;font-size:21px">FULL SYNTHETIC</div>
    <div class="abs advanced" style="left:0;width:352px;text-align:center;top:302px;font-size:20px">MOST ADVANCED</div>
    <div class="abs performance" style="left:92px;top:327px;width:168px;height:24px;padding-top:3px;font-size:18px">PERFORMANCE</div>
    <div class="abs tagline" style="left:0;width:352px;top:358px">MAXIMUM PROTECTION<br>FOR MORE MILES</div>

    <div class="seal" style="left:28px;top:504px;width:98px;height:98px" role="img" aria-label="Gasoline engine certification seal"></div>

    <div class="abs grade-sae" style="left:352px;top:327px">SAE</div>
    <div class="abs grade-big" style="left:436px;top:362px">5W-30</div>
    <div class="abs grade-spec" style="left:342px;top:530px">ALI SN</div>

    <div class="abs volume" style="left:35px;top:703px">32oz 1946mU</div>
    <div class="abs made-usa" style="left:224px;top:706px;width:110px">Made In USA<small>★★★</small></div>
  </section>

  <!-- BACK LABEL -->
  <section class="label label--back" aria-label="Back label">
    <svg class="label__art" viewBox="0 0 467 760" aria-hidden="true">
      <path d="M262 0H467V94C425 48 350 12 262 0Z" fill="var(--blue)"/>
      <path d="M178 0H262C350 12 425 48 467 94V120C410 55 300 12 178 0Z" fill="var(--red)"/>
    </svg>

    <div class="brand-dot" style="left:48px;top:38px;width:12px;height:12px"></div>
    <div class="abs brand-name" style="left:64px;top:34px;font-size:25px;letter-spacing:.5px">CORVANA</div>
    <div class="abs brand-sub" style="left:114px;top:72px;font-size:10px">MOTOR OIL</div>
    <div class="abs synthetic" style="left:50px;top:96px;font-size:12px;-webkit-text-stroke:.8px var(--ink)">FULL SYNTHETIC</div>
    <div class="abs mini-sae" style="left:50px;top:138px">SAE</div>
    <div class="abs mini-grade" style="left:63px;top:106px">5W-30</div>
    <div class="abs mini-spec" style="left:128px;top:146px">ALI SN</div>

    <div class="abs advanced" style="left:202px;top:117px;font-size:13px">MOST ADVANCED</div>
    <div class="abs performance" style="left:208px;top:134px;width:116px;height:16px;padding-top:2px;font-size:12px">PERFORMANCE</div>

    <div class="seal" style="left:352px;top:74px;width:76px;height:76px" role="img" aria-label="Gasoline engine certification seal"></div>

    <div class="abs copy copy--main">
      <p><span class="hl-red">CORVANA MOTOR OIL</span> <span class="hl-blue">5W30 and SAE</span> <b>Full Synthetic Motor Oil provides the ultimate performance and protection, especially under severe driving conditions.</b> It utilized newly developed additive technology to achieve among the lowest retes of wear ever for motor oils, well exceeding the most stringent North American specifications for wear control, cleanliness and sludge, oxidation control, and emission system and seal compatibility, while meeting the standards for fuel economy.</p>
      <p><span class="hl-blue">Licensed IRLSC GF-5 and ALI SN</span> “Resource Conserving” by the Allied Lubricant Institute (ALI) as all previous service classification. It is compatible with all conventional and synthetic oils.</p>
      <ul class="benefits">
        <li>Provides Protections That Conventional Oils Can’t</li>
        <li>Won’t Break Down Under Extreme Temperature</li>
        <li>Superior Protection For Extended Service Intervals.</li>
      </ul>
    </div>

    <div class="abs copy copy--small" style="top:461px">
      <span class="hl-red" style="font-weight:400">CORVANA MOTOR OIL</span> is manufactured to stringent standards. Every batch is tested, from raw materials to finished product, to insure you’re getting the Best Protection and Highest Performance from every quart.
    </div>
    <div class="abs copy copy--small" style="top:544px">
      <span class="title">Warning! Avoid skin contact with used motor oil!</span><br>
      Used moter oils have caused skin cancer in laboratory, animals when repeatedly applied and left in place between applications, In case of skin contact promptly wash thoroughly with soap and water, Oil soild clothing should be cleand before reuse
    </div>
    <div class="abs copy copy--small" style="top:642px;text-align:left">
      DON’T POLLUTE! Conserve resources<br>Take used oil to collection center.
    </div>

    <div class="abs sus" style="left:362px;top:461px">SUS 350</div>
    <div class="abs spec-box" style="left:351px;top:485px;width:100px;height:176px"></div>
    <div class="flag" style="left:351px;top:666px" role="img" aria-label="United States flag"></div>
    <div class="abs flag-caption" style="left:351px;top:718px;width:100px">MADE IN USA</div>
  </section>

</main>
</body>
</html>
```